Brintel Works - Fast, Efficient and Gas Mainteance for Domestic, Commercial and Industrial clients

We are in the process of purchasing a new business and would like to get a new logo and business card.
Business is a gas maintenance business that also does new gas installations.
Has been established since 1988.
Services include:
Install all types of gas appliances & equipment inc. hot water units
Maintain / repair / replace all types of gas appliances & equipment

Target Market(s)

Domestic, Commercial and Industrial clients

Industry/Entity Type

Business

Contact Information for Business Card

admin@brintelworks.com.au
07 3918 4726
Brintel Works PTY LTD

Logo Text

Gas Fitting & Plumbing Maintenance Specialists

Font styles to use
Sans Serif

Requirements
Must have
• Logo
• Business name, contact number, email address, web address
• Domestic | Commercial | Industrial Est Since 1988
Nice to have
• Possibly a black card with a flame logo to one side
Should not have
• Spelling errors

```html
<!DOCTYPE html>
<html lang="en">
<head>
<meta charset="utf-8">
<title>Brintel Works PTY LTD – Business Card</title>
<link rel="stylesheet" href="https://fonts.googleapis.com/css2?family=Didact+Gothic&family=PT+Sans&display=swap">
<style>
  :root {
    --stage: #2b2b2b;
    --card: #000000;
    --brand-yellow: #f7d400;
    --flame-red: #e8262a;
    --flame-orange: #f47b20;
    --text-light: #ffffff;
  }
  * { margin: 0; padding: 0; box-sizing: border-box; }
  html, body {
    width: 1200px;
    height: 900px;
    overflow: hidden;
    background: var(--stage);
  }
  .canvas {
    position: relative;
    width: 1200px;
    height: 900px;
  }
  .card {
    position: absolute;
    top: 184px;
    width: 302px;
    height: 490px;
    background: var(--card);
    border-radius: 12px;
  }
  .card--front { left: 299px; }
  .card--back { left: 646px; }

  .brand {
    display: flex;
    align-items: center;
    gap: 12px;
    font-family: "Didact Gothic", sans-serif;
    color: var(--brand-yellow);
    white-space: nowrap;
  }
  .brand__dot {
    flex: none;
    border-radius: 50%;
    background: var(--flame-red);
  }
  .card--front .brand {
    position: absolute;
    left: 34px;
    top: 118px;
    font-size: 33px;
  }
  .card--front .brand__dot { width: 26px; height: 26px; }

  .card--back .brand {
    position: absolute;
    left: 0;
    right: 0;
    top: 282px;
    flex-direction: column;
    gap: 18px;
    font-size: 36px;
  }
  .card--back .brand__dot { width: 40px; height: 40px; }

  .details {
    position: absolute;
    left: 0;
    right: 0;
    top: 244px;
    text-align: center;
    font-family: "PT Sans", sans-serif;
    font-size: 13.5px;
    line-height: 18px;
    color: var(--text-light);
  }
  .contact-list { list-style: none; }
  .contact-list li {
    display: flex;
    justify-content: center;
    align-items: center;
    gap: 6px;
  }
  .contact-list svg { width: 10px; height: 10px; flex: none; }
  .address, .sectors { margin-top: 20px; }
</style>
</head>
<body>
<main class="canvas">
  <section class="card card--front" aria-label="Business card front">
    <div class="brand">
      <span class="brand__dot"></span>
      <span class="brand__name">Brintel Works</span>
    </div>
    <div class="details">
      <ul class="contact-list">
        <li>
          <svg viewBox="0 0 10 10" aria-hidden="true"><path d="M2 0.5 L3.6 2.4 L2.8 3.6 Q4 6 6.4 7.2 L7.6 6.4 L9.5 8 L8.2 9.5 Q3.5 9 0.5 1.8 Z" fill="var(--flame-orange)"/></svg>
          <span>07 3918 4726</span>
        </li>
        <li>
          <svg viewBox="0 0 10 10" aria-hidden="true"><rect x="0.5" y="2" width="9" height="6.5" fill="var(--flame-orange)"/><path d="M0.5 2 L5 5.6 L9.5 2" fill="none" stroke="#000" stroke-width="0.9"/></svg>
          <span>admin@brintelworks.com.au</span>
        </li>
        <li>
          <svg viewBox="0 0 10 10" aria-hidden="true"><circle cx="5" cy="5" r="4.5" fill="var(--flame-orange)"/><path d="M0.5 5 H9.5 M5 0.5 Q2 5 5 9.5 M5 0.5 Q8 5 5 9.5" fill="none" stroke="#000" stroke-width="0.7"/></svg>
          <span>www.brintelworks.com.au</span>
        </li>
      </ul>
      <p class="address">12345, Address Goes Here<br>Country Name, 123456.</p>
      <p class="sectors">Domestic | Commercial<br>Industrial Est Since 1988</p>
    </div>
  </section>

  <section class="card card--back" aria-label="Business card back">
    <div class="brand">
      <span class="brand__dot"></span>
      <span class="brand__name">Brintel Works</span>
    </div>
  </section>
</main>
</body>
</html>
```